Every Shelf Set Neatly or ESN Organized needs a business card design. ESN Organized is a professi

We need a business card design that is clean, sharp and conveys a sense of organization. I already have a logo.

Target Market(s)

Families (specifically mothers), small business owners, parents, seniors

Industry/Entity Type

Business

Contact Information for Business Card

My website is www.esnorganized-example.com and my Facebook page is http://www.sociallink-example.com/everyshelfsetneatly. The phone number is 418-552-7094 and I want to be listed as Lorna M. Pelham, Owner

Requirements
Must have
• My logo.

```html
<!DOCTYPE html>
<html lang="en">
<head>
<meta charset="utf-8">
<title>Every Shelf Set Neatly – Business Card</title>
<link rel="stylesheet" href="https://fonts.googleapis.com/css2?family=Source+Sans+3:ital,wght@0,400;0,600;0,700;1,400&display=swap">
<style>
  :root {
    --page-bg: #e9e9ea;
    --card-bg: #f7f7f8;
    --brand-blue: #1a73d9;
    --ink: #1d1d1f;
    --text-grey: #3a3a3c;
    --band-text: #ffffff;
  }
  * { box-sizing: border-box; margin: 0; padding: 0; }
  html, body {
    width: 1200px;
    height: 900px;
    overflow: hidden;
    background: var(--page-bg);
    font-family: "Source Sans 3", sans-serif;
  }
  .card {
    position: absolute;
    left: 120px;
    top: 150px;
    width: 960px;
    height: 600px;
    background: var(--card-bg);
    box-shadow: 0 10px 30px rgba(0,0,0,0.12);
    overflow: hidden;
  }
  .brand {
    position: absolute;
    top: 78px;
    left: 0;
    width: 100%;
    display: flex;
    justify-content: center;
    align-items: center;
    gap: 22px;
  }
  .brand-square {
    width: 46px;
    height: 46px;
    background: var(--brand-blue);
  }
  .brand-name {
    font-size: 52px;
    font-weight: 400;
    letter-spacing: 3px;
    color: var(--ink);
    line-height: 1;
  }
  .owner {
    position: absolute;
    top: 212px;
    width: 100%;
    text-align: center;
  }
  .owner-name {
    font-size: 32px;
    font-weight: 700;
    color: var(--brand-blue);
    text-transform: uppercase;
    letter-spacing: 0.5px;
    line-height: 1.1;
  }
  .owner-title {
    font-size: 25px;
    color: var(--text-grey);
    margin-top: 4px;
  }
  .contact-icons {
    position: absolute;
    top: 312px;
    width: 100%;
    display: flex;
    justify-content: center;
    gap: 12px;
  }
  .contact-icons svg { width: 24px; height: 24px; fill: var(--brand-blue); }
  .contact-list {
    position: absolute;
    top: 348px;
    width: 100%;
    text-align: center;
    list-style: none;
    font-size: 25px;
    line-height: 37px;
    color: var(--text-grey);
  }
  .social-band {
    position: absolute;
    left: 182px;
    top: 483px;
    width: 596px;
    height: 99px;
  }
  .social-band svg { position: absolute; inset: 0; width: 100%; height: 100%; }
  .social-link {
    position: relative;
    display: flex;
    height: 100%;
    align-items: center;
    justify-content: center;
    font-size: 25px;
    font-style: italic;
    color: var(--band-text);
  }
</style>
</head>
<body>
  <div class="card">
    <div class="brand">
      <span class="brand-square"></span>
      <span class="brand-name">Every Shelf Set Neatly</span>
    </div>

    <div class="owner">
      <p class="owner-name">Lorna M. Pelham</p>
      <p class="owner-title">Owner</p>
    </div>

    <div class="contact-icons" aria-hidden="true">
      <svg viewBox="0 0 24 24"><path d="M6.6 10.8a15.1 15.1 0 0 0 6.6 6.6l2.2-2.2c.3-.3.7-.4 1-.2 1.1.4 2.3.6 3.6.6.6 0 1 .4 1 1V20c0 .6-.4 1-1 1C10.6 21 3 13.4 3 4c0-.6.4-1 1-1h3.5c.6 0 1 .4 1 1 0 1.3.2 2.5.6 3.6.1.3 0 .7-.2 1l-2.3 2.2z"/></svg>
      <svg viewBox="0 0 24 24"><path d="M2 5h20v14H2z M3.5 6.5 12 13l8.5-6.5" fill="none" stroke="#1a73d9" stroke-width="2"/><path d="M2 5h20v14H2z" fill="#1a73d9"/><path d="M3 6l9 7 9-7" fill="none" stroke="#f7f7f8" stroke-width="1.6"/></svg>
      <svg viewBox="0 0 24 24"><circle cx="12" cy="12" r="10"/><path d="M2 12h20M12 2c3 3 3 17 0 20M12 2c-3 3-3 17 0 20" fill="none" stroke="#f7f7f8" stroke-width="1.3"/></svg>
    </div>

    <ul class="contact-list">
      <li>418-552-7094</li>
      <li>info@esnorganized-example.com</li>
      <li>www.esnorganized-example.com</li>
    </ul>

    <div class="social-band">
      <svg viewBox="0 0 596 99" preserveAspectRatio="none" aria-hidden="true">
        <path d="M0 0 H596 Q572 50 596 99 H0 Q24 50 0 0 Z" fill="var(--brand-blue)"/>
      </svg>
      <p class="social-link">www.sociallink-example.com/everyshelfsetneatly</p>
    </div>
  </div>
</body>
</html>
```